Yacht, Boats, Watersports company needs a redesign of business card

Hello Designers!
We are a Boat dealership company that sells fun in the water, we sell boats, Yachts, Kayaks and also yacht WaterSport toys. We are looking to redesign our business cards in to something a little bit more sophisticated. in a way that we can make better use of our company colors. I'm attaching a zipped file containing the company 3 sets of company logo which one is an horizontal another one is a vertical and also a chromed 3d logo. Also is included two set of business cards that we use and also some designs that i think it's interesting. We use PMS 2026c Orange and PMS 7687C Blue. I would like to see at least two different options with the orange as accent and also using blue as an accent color. It's really important for the business cards to have a font option and size that is legible to most people. Our current website is wwww.coralpennant.com. Please visit if you want to have a better feeling of the Boat dealership
You can send Single sided or double side options. We are now using single sided but we may be open for a double side option if we really like the design.
Target Market(s)
Marine, boat sales, yacht sales, water toys sales/
Contact Information for Business Card
Name: Dale Whitcombe
Address: 212 North Fenwick Lane,
Gull Point, FL 32990
Phone: 555-731-8842
Fax: 954:731-8843
Cell: 555-382-1490
Email: dw@coralpennant.com
Website: coralpennant.com
Requirements
Must have
- the current information of the business card provided.
logo
use the PMS Colors
Nice to have
- a touch of elegance and sophistication but simple
Should not have
- should not have any typography that is hard to read, the card should be simple but yet sophisticated.

```html
<!DOCTYPE html>
<html lang="en">
<head>
<meta charset="utf-8">
<title>Coral Pennant business card</title>
<link href="https://fonts.googleapis.com/css2?family=Poppins:wght@400;500;600&display=swap" rel="stylesheet">
<style>
  :root {
    --backdrop: #dcdcdc;
    --blue-deep: #1b5ea9;
    --blue-light: #3d8bc9;
    --blue-text: #2f7cc0;
    --blue-ring: #15478a;
    --orange-light: #f6a94a;
    --orange-deep: #e8741c;
    --ink-grey: #555a60;
    --white: #ffffff;
  }
  html, body {
    margin: 0;
    width: 1200px;
    height: 1200px;
    overflow: hidden;
    background: var(--backdrop);
    font-family: "Poppins", sans-serif;
  }
  .card {
    position: absolute;
    left: 257px;
    width: 686px;
    height: 392px;
    border-radius: 24px;
    overflow: hidden;
  }
  .card svg { display: block; width: 100%; height: 100%; }
  .card-front { top: 165px; }
  .card-back { top: 653px; }
  .brand-name { font-family: "Poppins", sans-serif; font-weight: 600; fill: var(--white); }
  .holder-name { font-family: "Poppins", sans-serif; font-weight: 500; fill: var(--blue-text); }
  .contact-line { font-family: "Poppins", sans-serif; font-weight: 400; fill: var(--ink-grey); }
  .back-url { font-family: "Poppins", sans-serif; font-weight: 400; fill: var(--white); letter-spacing: 4.5px; }
  .icon { fill: var(--blue-text); }
</style>
</head>
<body>

<section class="card card-front" aria-label="Business card front">
  <svg viewBox="0 0 800 457" xmlns="http://www.w3.org/2000/svg">
    <defs>
      <linearGradient id="blueField" x1="0" y1="1" x2="1" y2="0">
        <stop offset="0" stop-color="var(--blue-deep)"/>
        <stop offset="1" stop-color="var(--blue-light)"/>
      </linearGradient>
      <linearGradient id="orangeBand" x1="0" y1="1" x2="1" y2="0">
        <stop offset="0" stop-color="var(--orange-deep)"/>
        <stop offset="1" stop-color="var(--orange-light)"/>
      </linearGradient>
    </defs>
    <rect class="blue-field" width="800" height="457" fill="url(#blueField)"/>
    <polygon class="accent-stripe" points="706,0 722,0 152,457 134,457" fill="url(#orangeBand)"/>
    <polygon class="blue-pinstripe" points="722,0 734,0 162,457 152,457" fill="var(--blue-text)"/>
    <polygon class="white-panel" points="734,0 800,0 800,457 162,457" fill="var(--white)"/>

    <g class="brand-block">
      <circle cx="202" cy="93" r="40" fill="none" stroke="var(--white)" stroke-width="6"/>
      <text class="brand-name" x="206" y="182" font-size="25" text-anchor="middle">CORAL PENNANT</text>
    </g>

    <text class="holder-name" x="748" y="255" font-size="26" text-anchor="end">DALE WHITCOMBE</text>
    <g class="contact-list" font-size="18">
      <text class="contact-line" x="723" y="291" text-anchor="end">555-731-8842</text>
      <text class="contact-line" x="723" y="314" text-anchor="end">555-382-1490</text>
      <text class="contact-line" x="723" y="336" text-anchor="end">555-731-8843</text>
      <text class="contact-line" x="723" y="359" text-anchor="end">dw@coralpennant.com</text>
      <text class="contact-line" x="723" y="381" text-anchor="end">www.coralpennant.com</text>
      <text class="contact-line" x="723" y="404" text-anchor="end">212 North Fenwick Lane, Gull Point, FL 32990</text>
    </g>
    <g class="contact-icons">
      <path class="icon" d="M733 277 q2 -2 4 0 l2 3 q1 2 -1 3 q1 3 4 5 q1 -2 3 -1 l3 2 q2 2 0 4 q-2 2 -5 1 q-7 -3 -10 -10 q-1 -3 0 -7z"/>
      <rect class="icon" x="735" y="298" width="10" height="17" rx="2"/>
      <rect x="737" y="300" width="6" height="11" fill="var(--white)"/>
      <rect class="icon" x="732" y="325" width="16" height="9" rx="1"/>
      <rect class="icon" x="735" y="320" width="9" height="6"/>
      <rect class="icon" x="732" y="348" width="15" height="10" rx="1"/>
      <path d="M732 349 l7.5 5 l7.5 -5" stroke="var(--white)" stroke-width="1.3" fill="none"/>
      <circle class="icon" cx="740" cy="376" r="7.5"/>
      <path d="M733 376 h14 M740 368.5 q-4 7.5 0 15 M740 368.5 q4 7.5 0 15" stroke="var(--white)" stroke-width="1" fill="none"/>
      <path class="icon" d="M740 406 q-7 -8 -7 -12 a7 7 0 0 1 14 0 q0 4 -7 12z"/>
      <circle cx="740" cy="394" r="2.5" fill="var(--white)"/>
    </g>
  </svg>
</section>

<section class="card card-back" aria-label="Business card back">
  <svg viewBox="0 0 800 457" xmlns="http://www.w3.org/2000/svg">
    <defs>
      <linearGradient id="blueBack" x1="0" y1="1" x2="1" y2="0">
        <stop offset="0" stop-color="var(--blue-deep)"/>
        <stop offset="1" stop-color="var(--blue-light)"/>
      </linearGradient>
    </defs>
    <rect width="800" height="457" fill="url(#blueBack)"/>
    <circle cx="400" cy="218" r="140" fill="none" stroke="var(--blue-ring)" stroke-width="14"/>
    <text class="brand-name" x="400" y="228" font-size="30" text-anchor="middle">CORAL PENNANT</text>
    <text class="back-url" x="400" y="420" font-size="17" text-anchor="middle">WWW.CORALPENNANT.COM</text>
  </svg>
</section>

</body>
</html>
```